Natural Supplement Co Needs Label Makeover

Our company's success began with our main product, an amino acid blend that aids in fat metabolism, called Vantorel. Since then we continue to expand the product line that now includes a detox called Vantopurge, and probiotic called Vantoflora, as well as 3 others, for a total of 6 products/ labels.
Our original design/logo had more of an 'old-timey' feel (see attached 2-product photo). We are looking for a fresh label design update for the product line which reflects the range of supplements as cohesive and individual parts of an overall health plan/strategy (see attached 'Logo Update Test' as just one idea we had in-house, you need not consider it as a starting point).

Target Market(s)

women 25-45

Industry/Entity Type

Health And Wellness

Requirements
Must have
• consistent theme with confident look
Nice to have
• Each product (ie. "Vantorel") has a few-word descriptor: ("Fat-Burning Amino Acids") that should be planned on including as part of each label.
Should not have
• NO 'streamlined' or graphic interpretations of the human body, or figurative image

```html
<!DOCTYPE html>
<html lang="en">
<head>
<meta charset="utf-8">
<title>Vantoflora Label</title>
<link rel="stylesheet" href="https://fonts.googleapis.com/css2?family=Bree+Serif&family=Fira+Sans:wght@600&family=Oswald:wght@300&display=swap">
<style>
  :root {
    --backdrop: #ececec;
    --label-white: #ffffff;
    --purple-deep: #5b2a86;
    --purple-mid: #7a3aa6;
    --purple-light: #8d4bb8;
    --band-yellow: #eef03a;
    --band-yellow-edge: #d9db22;
    --ink-dark: #3a3a3a;
    --band-black: #111111;
    --text-white: #ffffff;
    --text-grey: #7a7a7a;
    --rule: rgba(255,255,255,0.85);
  }
  * { margin: 0; padding: 0; box-sizing: border-box; }
  html, body {
    width: 960px; height: 1200px; overflow: hidden;
    background: var(--backdrop);
  }
  .label {
    position: absolute; left: 160px; top: 117px;
    width: 640px; height: 966px;
    background: var(--label-white);
    box-shadow: 0 2px 10px rgba(0,0,0,0.08);
  }
  .label__panel {
    position: absolute; left: 50px; top: 0;
    width: 540px; height: 723px;
    background: linear-gradient(100deg, var(--purple-deep) 0%, var(--purple-mid) 55%, var(--purple-light) 75%, var(--purple-mid) 100%);
  }
  .label__descriptor-band {
    position: absolute; left: 0; top: 108px;
    width: 640px; height: 162px;
    background: linear-gradient(180deg, var(--band-yellow) 0%, var(--band-yellow) 85%, var(--band-yellow-edge) 100%);
    display: flex; align-items: center; justify-content: center;
  }
  .label__descriptor {
    font-family: "Bree Serif", serif;
    font-size: 66px; color: var(--ink-dark);
    letter-spacing: 0.5px;
  }
  .label__product-name {
    position: absolute; left: 0; top: 350px; width: 640px;
    text-align: center;
    font-family: "Fira Sans", sans-serif; font-weight: 600;
    font-size: 112px; line-height: 1; color: var(--text-white);
    letter-spacing: -1px;
  }
  .label__rule {
    position: absolute; left: 85px; width: 470px; height: 2px;
    background: var(--rule);
  }
  .label__rule--top { top: 557px; }
  .label__rule--bottom { top: 664px; }
  .label__ingredient {
    position: absolute; left: 0; top: 585px; width: 640px;
    text-align: center;
    font-family: "Bree Serif", serif;
    font-size: 44px; color: var(--text-white); letter-spacing: 1px;
  }
  .label__claim-band {
    position: absolute; left: 0; top: 723px;
    width: 640px; height: 81px;
    background: var(--band-black);
    display: flex; align-items: center; justify-content: center;
  }
  .label__claim {
    font-family: "Bree Serif", serif;
    font-size: 34px; color: var(--text-white); letter-spacing: 0.5px;
  }
  .label__volume {
    position: absolute; left: 0; top: 866px; width: 640px;
    text-align: center;
    font-family: "Oswald", sans-serif; font-weight: 300;
    font-size: 28px; color: var(--text-grey);
  }
</style>
</head>
<body>
  <main class="label">
    <div class="label__panel"></div>
    <div class="label__descriptor-band">
      <span class="label__descriptor">Fat Burning</span>
    </div>
    <h1 class="label__product-name">Vantoflora</h1>
    <div class="label__rule label__rule--top"></div>
    <p class="label__ingredient">AMINO ACIDS</p>
    <div class="label__rule label__rule--bottom"></div>
    <div class="label__claim-band">
      <span class="label__claim">ALL NATURAL SUPPLEMENT</span>
    </div>
    <p class="label__volume">1 FL. OZ (30 ml)</p>
  </main>
</body>
</html>
```